Business card for Luxury Portable Restroom Trailer company

We are a Luxury Portable Restroom Trailer Company Called FALCRIDGE HIRES. Based in Orange County California. We provide portable restroom trailers for events, such as, Weddings, Concerts, Charity events, Sporting events, Tournaments, Corporate events, ect. We rent and Sell the Luxury restrooms. Our colors are white, grey, and Orange. As you will see in the logo we uploaded.
There are 2 people in the company so the names and titles will change for the 3 people but card will remain the same. Here is the information for each Person: Dwight Penner CFO 555 318-0476
next Person: Leon Marchetti VP 555 318-0476
Next Person: Owen Marchetti CEO 555 318-0476
Information to include on the card: Luxury Restroom Trailers Rental and Sales. Weddings, Concerts, Charity, Sporting and Corp. Events.

```html
<!DOCTYPE html>
<html lang="en">
<head>
<meta charset="utf-8">
<title>Falcridge Hires – Business Card</title>
<link href="https://fonts.googleapis.com/css2?family=Montserrat:wght@400;500;700;800&display=swap" rel="stylesheet">
<style>
  :root {
    --backdrop: #1b1b1c;
    --card: #242425;
    --card-sheen: #2c2c2d;
    --orange: #f26a1b;
    --white: #f4f4f4;
    --grey: #5a5a5c;
    --grey-dark: #333335;
  }
  * { box-sizing: border-box; margin: 0; padding: 0; }
  html, body {
    width: 1200px; height: 801px; overflow: hidden;
    background: var(--backdrop);
    font-family: "Montserrat", sans-serif;
  }
  .sheet {
    width: 1200px; height: 801px;
    display: flex; align-items: center; justify-content: center; gap: 40px;
  }
  .card {
    position: relative;
    width: 540px; height: 309px;
    background: linear-gradient(135deg, var(--card-sheen), var(--card) 60%);
    border-bottom: 4px solid var(--orange);
    overflow: hidden;
  }

  /* Front */
  .brand {
    position: absolute; left: 34px; top: 34px;
    display: flex; align-items: center; gap: 8px;
    font-weight: 800; font-size: 22px; letter-spacing: 1px;
    color: var(--orange);
  }
  .brand-square { width: 14px; height: 14px; background: var(--orange); }
  .emblem {
    position: absolute; right: 44px; top: 26px;
    width: 110px; height: 110px; border-radius: 50%;
    background: radial-gradient(circle at 40% 35%, #3a3a3c, #202021);
    border: 2px solid var(--grey-dark);
  }
  .person { position: absolute; left: 34px; top: 128px; }
  .person-name {
    font-weight: 700; font-size: 24px; letter-spacing: 1px;
    color: var(--orange);
  }
  .person-title { font-weight: 500; font-size: 14px; color: var(--white); margin-top: 4px; }
  .divider {
    position: absolute; left: 34px; right: 34px; top: 200px;
    height: 1px; background: var(--orange);
  }
  .contacts {
    position: absolute; left: 34px; right: 34px; top: 222px;
    display: flex; justify-content: space-between; align-items: flex-end;
  }
  .contact-list { display: flex; flex-direction: column; gap: 9px; }
  .contact {
    display: flex; align-items: center; gap: 8px;
    font-size: 13px; font-weight: 400; color: var(--white);
  }
  .contact svg { width: 12px; height: 12px; flex: none; }

  /* Back */
  .back { display: flex; flex-direction: column; align-items: center; justify-content: center; }
  .back-brand {
    font-weight: 800; font-size: 40px; letter-spacing: 3px;
    color: var(--grey);
    margin-bottom: 44px;
  }
  .tagline { font-weight: 700; font-size: 15px; color: var(--orange); }
  .services { font-weight: 500; font-size: 14px; color: var(--white); margin-top: 6px; }
</style>
</head>
<body>
<main class="sheet">
  <section class="card front">
    <div class="brand"><span class="brand-square"></span>FALCRIDGE HIRES</div>
    <div class="emblem"></div>
    <div class="person">
      <p class="person-name">OWEN MARCHETTI</p>
      <p class="person-title">CEO</p>
    </div>
    <div class="divider"></div>
    <div class="contacts">
      <div class="contact-list">
        <p class="contact">
          <svg viewBox="0 0 12 12" aria-hidden="true"><path d="M2.5 1h2l1 2.5-1.3 1a6 6 0 0 0 3.3 3.3l1-1.3L11 7.5v2A1.5 1.5 0 0 1 9.5 11 8.5 8.5 0 0 1 1 2.5 1.5 1.5 0 0 1 2.5 1z" fill="var(--orange)"/></svg>
          555 318-0476
        </p>
        <p class="contact">
          <svg viewBox="0 0 12 12" aria-hidden="true"><rect x="1" y="2.5" width="10" height="7" fill="var(--orange)"/><path d="M1 2.5 6 6.5l5-4" stroke="var(--card)" stroke-width="1" fill="none"/></svg>
          owen@falcridgehires.com
        </p>
      </div>
      <p class="contact">
        <svg viewBox="0 0 12 12" aria-hidden="true"><circle cx="6" cy="6" r="5" fill="none" stroke="var(--orange)" stroke-width="1.2"/><path d="M1 6h10M6 1c-2.5 3-2.5 7 0 10M6 1c2.5 3 2.5 7 0 10" stroke="var(--orange)" stroke-width="1" fill="none"/></svg>
        www.falcridgehires.com
      </p>
    </div>
  </section>

  <section class="card back">
    <p class="back-brand">FALCRIDGE HIRES</p>
    <p class="tagline">Luxury Restroom Trailers Rental and Sales</p>
    <p class="services">Weddings | Concerts | Charity | Sporting | Corp</p>
  </section>
</main>
</body>
</html>
```